Business card for a Exhibition booth fabrication company

Hi. My company would like to change our corporate name card. We are an events and Exhibition stand builder company. We would like our corporate name card to resonate what we do. I need someone to create something unique that relates to the industry that I am in. The graphic designer should be creative to incorporate the elements of my industry and try to blend in well in the design of the card. Our aim is to ensure that we are unique and our card can look different from our competitors.
Updates

Target Market(s)

Marketing and events manager from all companies

Contact Information for Business Card

The business card should have the following details:
Name
Job Title
Email
Website

Colors

Designer to choose colors to be used in the design.

Requirements
Must have
• The card must be look something that is relevant to the service that I am providing. My website is: www.velmora-buildworks.com
• You can see my website to get more information on what service that I am doing
Nice to have
• On the back of my card, I would like to have a globe image with the incorporation of my company logo. This is to indicate that my services can be done in any part of the world.

```html
<!DOCTYPE html>
<html lang="en">
<head>
<meta charset="utf-8">
<title>Velmora Buildworks – Business Card</title>
<link rel="stylesheet" href="https://fonts.googleapis.com/css2?family=Montserrat:wght@600;700&family=Open+Sans:wght@400;600&display=swap">
<style>
  :root {
    --brand-red: #e8202a;
    --ink-grey: #58595b;
    --swoosh-grey: #8a8b8d;
    --card-white: #ffffff;
    --backdrop: #e9e6e2;
    --map-dot: #e4e4e4;
  }
  * { margin: 0; padding: 0; box-sizing: border-box; }
  html, body { width: 1200px; height: 997px; overflow: hidden; }
  body {
    background: var(--backdrop);
    font-family: "Open Sans", Arial, sans-serif;
    position: relative;
  }
  .card {
    position: absolute;
    left: 250px;
    width: 700px;
    height: 400px;
    background: var(--card-white);
    box-shadow: 0 6px 18px rgba(0,0,0,.12);
    overflow: hidden;
  }
  .card--front { top: 80px; }
  .card--back { top: 517px; }

  .card__waves { position: absolute; inset: 0; width: 100%; height: 100%; }

  .brand-name {
    font-family: "Montserrat", Arial, sans-serif;
    font-weight: 700;
    color: var(--ink-grey);
    letter-spacing: 3px;
    display: flex;
    align-items: center;
    gap: 12px;
    white-space: nowrap;
  }
  .brand-name__dot {
    width: 16px; height: 16px; border-radius: 50%;
    background: var(--brand-red);
  }
  .card--front .brand-name {
    position: absolute; left: 48px; top: 150px; font-size: 20px;
  }

  .person { position: absolute; right: 48px; top: 46px; text-align: right; }
  .person__name {
    font-family: "Montserrat", Arial, sans-serif;
    font-weight: 600; font-size: 17px; color: var(--ink-grey); letter-spacing: .5px;
  }
  .person__title { font-size: 13px; color: var(--brand-red); font-weight: 600; }

  .contact-list {
    position: absolute; right: 48px; top: 140px;
    list-style: none; font-size: 14px; color: var(--ink-grey);
  }
  .contact-list li {
    display: flex; align-items: center; justify-content: flex-end; gap: 7px;
    line-height: 22px;
  }
  .contact-list svg { width: 11px; height: 11px; fill: var(--brand-red); }

  .address {
    position: absolute; left: 48px; bottom: 28px;
    color: var(--card-white); font-size: 16px; line-height: 24px;
  }

  .world-map {
    position: absolute; left: 70px; top: 40px; width: 560px; height: 320px;
    border-radius: 40% 45% 38% 42%;
    background: radial-gradient(ellipse at center, var(--map-dot) 0%, rgba(228,228,228,.6) 55%, rgba(255,255,255,0) 75%);
  }
  .card--back .brand-name {
    position: absolute; left: 50%; top: 50%;
    transform: translate(-50%, -50%);
    font-size: 30px; letter-spacing: 4px;
  }
  .card--back .brand-name__dot { width: 24px; height: 24px; }
</style>
</head>
<body>

  <section class="card card--front" aria-label="Business card front">
    <svg class="card__waves" viewBox="0 0 700 400" preserveAspectRatio="none" aria-hidden="true">
      <path d="M0,286 C200,284 340,262 450,226 C560,190 640,222 700,220 L700,232 C640,234 560,204 450,240 C340,276 200,298 0,298 Z" fill="var(--swoosh-grey)"/>
      <path d="M0,304 C200,304 340,282 450,246 C560,210 640,240 700,238 L700,400 L0,400 Z" fill="var(--brand-red)"/>
    </svg>

    <div class="brand-name"><span class="brand-name__dot"></span>VELMORA BUILDWORKS</div>

    <div class="person">
      <p class="person__name">DANIEL REYES</p>
      <p class="person__title">President</p>
    </div>

    <ul class="contact-list">
      <li><svg viewBox="0 0 24 24"><path d="M6.6 10.8a15.1 15.1 0 0 0 6.6 6.6l2.2-2.2a1 1 0 0 1 1-.25 11.4 11.4 0 0 0 3.6.57 1 1 0 0 1 1 1V20a1 1 0 0 1-1 1A17 17 0 0 1 3 4a1 1 0 0 1 1-1h3.5a1 1 0 0 1 1 1c0 1.250.2 2.450.57 3.57a1 1 0 0 1-.25 1z"/></svg>+974 7000 4821</li>
      <li><svg viewBox="0 0 24 24"><path d="M2 5h20v14H2z M2 5l10 8 10-8" fill="var(--brand-red)"/></svg>info@velmora-buildworks.com</li>
      <li><svg viewBox="0 0 24 24"><circle cx="12" cy="12" r="10"/></svg>www.velmora-buildworks.com</li>
    </ul>

    <p class="address">P.O. Box 4120,<br>Corniche Road, Doha - Qatar</p>
  </section>

  <section class="card card--back" aria-label="Business card back">
    <div class="world-map" role="img" aria-label="Faint dotted world map behind the company name"></div>
    <div class="brand-name"><span class="brand-name__dot"></span>VELMORA BUILDWORKS</div>
  </section>

</body>
</html>
```